Corporate brochure design 4 pages

Hi,

We are a real estate company based in Europe.

We have almost finalized a rebranding.

We are developing a brand book guidelines (still on working process) to help you undertstand the look and feel of our new CI. I would like to receive proposals of design for a corporate brochure template. I need to receive the Indesign files with full ownership rights to be able to adapt all our documentation with this template.
Regarding the images, you can take gabaris on www.pelvarimages.example. I will be able to take them afterwards.

There will be 4 pages. you will receive the 4 pages on pdf for your consideration with our (almost) actual layout.

- 1st page: cover
- 2nd page: company presentation in french and english
- 3rd page: some market data + graph
- 4th page: 2 retail centers presentation.

In the template, i need to have:
- the paragraph styles in order
- 2 different masters with top/bottom/page number aso.

Please feel free to ask any other questions.

best regards,
Updates

I would like to precise tha t we are active on the commercial real estate sector:

- office transactions (rent /sales)
- property management of administrative and business buildings
- Valuation of properties
- Capital markets (investment advices for selling building)

Industry/Entity Type

Real Estate

Colors

Designer to choose colors to be used in the design.

```html
<!DOCTYPE html>
<html lang="en">
<head>
<meta charset="utf-8">
<title>Retail Centre – High Streets Luxembourg</title>
<link href="https://fonts.googleapis.com/css2?family=Arimo:wght@400;700&display=swap" rel="stylesheet">
<style>
  :root{
    --orange:#f07a2a;
    --orange-deep:#e8631a;
    --peach:#fdebe0;
    --ink:#111111;
    --text:#222222;
    --paper:#ffffff;
    --map-grey:#cfcfcf;
    --map-blue:#dfe7f1;
  }
  *{margin:0;padding:0;box-sizing:border-box}
  html,body{width:848px;height:1200px;overflow:hidden;background:var(--paper)}
  body{font-family:"Arimo",Arial,sans-serif;color:var(--text)}
  .page{position:relative;width:848px;height:1200px;overflow:hidden;background:var(--paper)}
  .swoosh{position:absolute;left:0;width:848px}
  .swoosh--top{top:0;height:90px}
  .swoosh--bottom{bottom:0;height:80px}
  .section-tag{position:absolute;left:320px;top:66px;width:208px;height:30px;border-radius:15px;background:var(--ink);color:#fff;font-weight:700;font-size:19px;letter-spacing:.5px;text-align:center;line-height:30px}
  .street-title{position:absolute;left:51px;font-size:24px;line-height:28px;font-weight:400;color:var(--ink);text-transform:uppercase}
  .photo{position:absolute;left:51px;width:308px;border:3px solid var(--orange)}
  .photo--city{top:200px;height:168px;background:linear-gradient(160deg,#8a8f6a 0%,#c9b27e 45%,#6f6a5a 100%)}
  .photo--station{top:745px;height:163px;background:linear-gradient(170deg,#c7cbd2 0%,#9a7f6f 45%,#4d4a4c 100%)}
  .map{position:absolute;left:477px;width:321px;border-radius:40% 45% 38% 50%;background:radial-gradient(circle at 50% 45%,var(--map-blue) 0%,var(--map-grey) 60%,#e8e8e8 100%)}
  .map--city{top:100px;height:250px}
  .map--station{top:635px;height:265px}
  .facts{position:absolute;left:51px;width:747px;border-collapse:collapse;font-size:12px;line-height:14.5px}
  .facts--city{top:388px}
  .facts--station{top:923px}
  .facts th,.facts td{text-align:left;vertical-align:top;font-weight:400;padding:4px 6px}
  .facts th{width:246px;color:var(--ink);white-space:nowrap}
  .facts td{padding-left:12px}
  .facts tr.is-accent th{background:var(--orange)}
  .facts tr.is-accent td{background:var(--peach)}
</style>
</head>
<body>
<div class="page">

  <svg class="swoosh swoosh--top" viewBox="0 0 848 90" preserveAspectRatio="none" aria-hidden="true">
    <path d="M0 0 H848 V10 C620 0 300 10 0 48 Z" fill="var(--ink)"/>
    <path d="M0 56 C260 20 560 10 848 16 V22 C560 20 300 34 0 68 Z" fill="var(--orange-deep)"/>
  </svg>

  <div class="section-tag">RETAIL CENTRE</div>

  <h1 class="street-title" style="top:100px">High Streets<br>Luxembourg:<br>City - Pedestrian Zone</h1>
  <div class="photo photo--city" role="img" aria-label="Photo of a busy pedestrian shopping street with banners"></div>
  <div class="map map--city" role="img" aria-label="Map of Luxembourg city locating the pedestrian zone and access roads"></div>

  <table class="facts facts--city">
    <tr class="is-accent"><th>Zone- Zone</th><td>Pedestrian area: Grand-Rue, Rue Philippe II…</td></tr>
    <tr><th>Stock- Stock</th><td>51 500 m²&nbsp;&nbsp; - sqm</td></tr>
    <tr class="is-accent"><th>Magasins- Shops</th><td>+/- 400</td></tr>
    <tr><th>Niveau loyers- Rental bands<br>(euros/sqm-m²/année-year)+TVA-VAT</th><td>960 – 1 320</td></tr>
    <tr class="is-accent"><th>Parking</th><td>3 800 (public)</td></tr>
    <tr><th>Marques principales- Main<br>brands</th><td>Quillon, Oberly &amp; Pask, Aurelio Venn, Maristelle, Torvane Horlogerie, Kaffeluna, Isoline Marre, Brisac &amp; Thorn, Crystelva (flagship store Benelux), Penhollow, Petitbrume, Velmara, Ondine Wear, Greenbite, Rook &amp; Bramble, Lumessa, Valdorne, Kestrel Hale, Ambrine, Quorvo, Thistle &amp; Tide, Ellory Wick, Silkmere, Pellacourt, Circuitry Hall (Orchard Tech), Vistaquay Optics, Marwenne, Fallowby, Albrecht Sorel, …</td></tr>
  </table>

  <h1 class="street-title" style="top:631px">High Streets<br>Luxembourg Station<br>Av. Gare</h1>
  <div class="photo photo--station" role="img" aria-label="Photo of a tree-lined avenue with shops and parked cars"></div>
  <div class="map map--station" role="img" aria-label="Map of Luxembourg city locating the station avenue and access roads"></div>

  <table class="facts facts--station">
    <tr class="is-accent"><th>Zone- Zone</th><td>Avenue de la Gare</td></tr>
    <tr><th>Stock- Stock</th><td>37 500 m²&nbsp;&nbsp; - sqm</td></tr>
    <tr class="is-accent"><th>Magasins- Shops</th><td>+/- 120</td></tr>
    <tr><th>Niveau loyers- Rental bands<br>(euros/sqm-m²/année-year)+TVA-VAT</th><td>300 – 720 euros/sqm/year</td></tr>
    <tr class="is-accent"><th>Parking</th><td>1 880 (public)</td></tr>
    <tr><th>Marques principales- Main<br>brands</th><td>Oberly &amp; Pask, Voltavia, Calloway Lane, Harborline, Maison Brevelle, Lisserand, Kittera, Q&amp;V, Dowsa, Nouk, Fil &amp; Bobine, Lumessa, Pas Léger, Velouté, Optimarre, Burgerquay, Pralinor, Dentellia, Herbelune, Rive Onze, Galerie Azurine, Fallowby, Orvelle, Marché Tillon, Inês Quarry, Halloran Tailors</td></tr>
  </table>

  <svg class="swoosh swoosh--bottom" viewBox="0 0 848 80" preserveAspectRatio="none" aria-hidden="true">
    <path d="M0 28 C300 22 600 30 848 62 V68 C600 38 300 30 0 34 Z" fill="var(--orange-deep)"/>
    <path d="M0 44 C320 36 620 50 848 74 V80 H0 Z" fill="var(--ink)"/>
  </svg>

</div>
</body>
</html>
```